Business Card - Tidal Lanes

Need Business Card design for company named Tidal Lanes. Software development focused mainly on Brindle Orvix & Zelt Apps. I've attached our logo with both a black and white background. Please add trademark symbol to logo when using.

```html
<!DOCTYPE html>
<html lang="en">
<head>
<meta charset="utf-8">
<title>Tidal Lanes – Business Card</title>
<link rel="stylesheet" href="https://fonts.googleapis.com/css2?family=Open+Sans:wght@400;600;700&display=swap">
<style>
  :root {
    --stage: #e9e4de;
    --card-dark: #050505;
    --ink-light: #ffffff;
    --accent-yellow: #f7b718;
    --accent-orange: #f39a2c;
    --accent-red: #e2321f;
    --text-muted: #f2f2f2;
  }
  * { box-sizing: border-box; margin: 0; padding: 0; }
  html, body {
    width: 1200px; height: 720px; overflow: hidden;
    background: var(--stage);
    font-family: "Open Sans", Arial, sans-serif;
  }
  .stage {
    position: relative; width: 1200px; height: 720px;
    display: flex; align-items: center; justify-content: center; gap: 40px;
  }
  .card {
    position: relative; width: 540px; height: 309px;
    box-shadow: 0 6px 18px rgba(0,0,0,.18);
    overflow: hidden;
  }
  /* Front side */
  .card--front { background: var(--card-dark); color: var(--ink-light); }
  .brand {
    position: absolute; left: 40px; top: 46px;
    display: flex; align-items: center; gap: 12px;
  }
  .brand__mark {
    width: 26px; height: 26px; background: var(--accent-orange);
  }
  .brand__name {
    font-size: 26px; font-weight: 700; color: var(--ink-light);
    letter-spacing: -0.5px;
  }
  .brand__name sup { font-size: 11px; vertical-align: top; }
  .contact {
    position: absolute; left: 40px; bottom: 40px;
    list-style: none; font-size: 14px; color: var(--text-muted);
  }
  .contact li { display: flex; align-items: center; gap: 8px; line-height: 24px; }
  .contact__icon { width: 12px; height: 14px; flex: none; }
  .contact__address { margin-top: 14px; }
  .person {
    position: absolute; right: 40px; top: 46px; text-align: left;
  }
  .person__name { font-size: 16px; font-weight: 700; color: var(--accent-yellow); }
  .person__title { font-size: 13px; color: var(--ink-light); margin-left: 70px; }
  /* Back side */
  .card--back {
    background: linear-gradient(100deg, var(--accent-yellow), var(--accent-orange));
    color: var(--ink-light);
    display: flex; flex-direction: column; align-items: center; justify-content: center;
  }
  .back-brand { display: flex; align-items: center; gap: 16px; margin-top: -10px; }
  .back-brand__mark { width: 40px; height: 40px; background: var(--ink-light); }
  .back-brand__name { font-size: 44px; font-weight: 700; letter-spacing: -1px; }
  .website {
    position: absolute; bottom: 38px; left: 0; right: 0; text-align: center;
    font-size: 14px; letter-spacing: 1.5px;
  }
</style>
</head>
<body>
<main class="stage">
  <section class="card card--front" aria-label="Card front">
    <div class="brand">
      <span class="brand__mark"></span>
      <span class="brand__name">Tidal Lanes<sup>™</sup></span>
    </div>
    <div class="person">
      <p class="person__name">Your Name</p>
      <p class="person__title">Title</p>
    </div>
    <ul class="contact">
      <li>
        <svg class="contact__icon" viewBox="0 0 12 14" aria-hidden="true"><rect x="2" y="0.5" width="8" height="13" rx="1.5" fill="none" stroke="#f7b718" stroke-width="1.4"/><rect x="4" y="2.5" width="4" height="6" fill="#f7b718"/></svg>
        555-014-2290
      </li>
      <li>
        <svg class="contact__icon" viewBox="0 0 12 14" aria-hidden="true"><path d="M3 1 L5 1 L6 4 L4.5 5.5 Q6 8.5 8.5 9.5 L10 8 L12 9.5 L12 12 Q6 13 2 6 Q1.5 3 3 1Z" fill="#f7b718"/></svg>
        555-018-6431
      </li>
      <li class="contact__address">2140 Harbor Row, Dunmore, FL 30219</li>
    </ul>
  </section>

  <section class="card card--back" aria-label="Card back">
    <div class="back-brand">
      <span class="back-brand__mark"></span>
      <span class="back-brand__name">Tidal Lanes</span>
    </div>
    <p class="website">www.tidallanes.com</p>
  </section>
</main>
</body>
</html>
```